Verpackungen für Sekt/Champagner Flaschen
Zielgruppe
Dekoration für Hochzeiten. Tisch Dekoration für Hochzeiten. Zielgruppe alles was mit Hochzeiten zutun hat
Aufgabenstellung
Wir lassen gerade ein Tube/Dose herstellen, die als Umverpackung oder einfach Verpackung für Sekt/Champagne Flaschen dienen soll die dann auf die Tische für Hochzeit´s Deko kommt um die die Tisch Deko aufzubessern, statt einfach nur eine Sekt Flasche stehen zu haben. .Die Tube wird komplett in weiß sein und alles andere an Design soll in einem Gold sein. Mr&Mrs oder Just Married mit Herzen und alles was sonst dazu gehört, da lassen wir freie Hand.
Das Design soll Schlicht sein aber auch Luxuriös.
Durchmesser der Tube wird 8,5 cm haben und 34-35 cm sein.
Die Goldene Schrift und das Muster soll am Ende in einem Relief Lack auf der Tube erscheinen

```html
<!DOCTYPE html>
<html lang="de">
<head>
<meta charset="utf-8">
<title>Mr&amp;Mrs – Banderole Sektverpackung</title>
<link rel="stylesheet" href="https://fonts.googleapis.com/css2?family=Cormorant+Garamond:wght@500&display=swap">
<style>
  :root {
    --paper: #ffffff;
    --gold: #c49a6c;
    --gold-text: #9a7650;
    --flourish-soft: #e9e2dc;
    --flourish-mid: #cfc3b9;
  }
  html, body {
    margin: 0;
    padding: 0;
    width: 1200px;
    height: 287px;
    overflow: hidden;
    background: var(--paper);
  }
  .banderole {
    position: relative;
    width: 1200px;
    height: 287px;
    background: var(--paper);
    overflow: hidden;
  }
  .rule {
    position: absolute;
    height: 7px;
    background: var(--gold);
  }
  .rule--left  { left: 0;     width: 440px; }
  .rule--right { left: 760px; width: 440px; }
  .rule--upper { top: 144px; }
  .rule--lower { top: 160px; }

  .flourish {
    position: absolute;
    width: 175px;
    height: 34px;
    border-radius: 17px;
    background: linear-gradient(90deg, var(--flourish-soft), var(--flourish-mid) 50%, var(--flourish-soft));
  }
  .flourish--left  { left: 105px; }
  .flourish--right { left: 860px; }
  .flourish--top    { top: 100px; }
  .flourish--bottom { top: 182px; }

  .title-frame {
    position: absolute;
    left: 462px;
    top: 74px;
    width: 271px;
    height: 138px;
    box-sizing: border-box;
    border: 6px solid var(--gold);
    display: flex;
    align-items: center;
    justify-content: center;
  }
  .title-frame__text {
    margin: 0;
    font-family: "Cormorant Garamond", serif;
    font-weight: 500;
    font-size: 64px;
    line-height: 1;
    letter-spacing: 1px;
    color: var(--gold-text);
    white-space: nowrap;
  }
</style>
</head>
<body>
  <main class="banderole">
    <div class="rule rule--left rule--upper"></div>
    <div class="rule rule--left rule--lower"></div>
    <div class="rule rule--right rule--upper"></div>
    <div class="rule rule--right rule--lower"></div>

    <div class="flourish flourish--left flourish--top" role="img" aria-label="Geschwungenes Zierornament über der linken Doppellinie"></div>
    <div class="flourish flourish--left flourish--bottom" role="img" aria-label="Geschwungenes Zierornament unter der linken Doppellinie"></div>
    <div class="flourish flourish--right flourish--top" role="img" aria-label="Geschwungenes Zierornament über der rechten Doppellinie"></div>
    <div class="flourish flourish--right flourish--bottom" role="img" aria-label="Geschwungenes Zierornament unter der rechten Doppellinie"></div>

    <div class="title-frame">
      <h1 class="title-frame__text">Mr&amp;Mrs</h1>
    </div>
  </main>
</body>
</html>
```